Tech business card design

We need an amazing business card design for our new business 'Pexla' a marketing tech startup based in Sydney, Australia. We provide an online marketplace for businesses to search and buy advertising media, connect with service providers and learn more about marketing. We wish to communicate 'cool tech', reliability and professionalism and design based around our logo.

Target Market(s)

Business Owners

Contact Information for Business Card

Name
Position
Email Address
Website
Phone Number

Font styles to use
Other font styles liked:
• Avenir & Avenir Next

Colors

Designer to choose colors to be used in the design.

```html
<!DOCTYPE html>
<html lang="en">
<head>
<meta charset="utf-8">
<title>Pexla Business Card</title>
<link href="https://fonts.googleapis.com/css2?family=Nunito+Sans:wght@400;600;800&display=swap" rel="stylesheet">
<style>
  :root {
    --bg: #3a3a3c;
    --navy: #10123d;
    --paper: #f4f4f5;
    --paper-shade: #dcdcde;
    --ink: #14163f;
    --muted: #6b6b72;
    --white: #ffffff;
    --divider: #55565c;
  }
  * { box-sizing: border-box; margin: 0; padding: 0; }
  html, body { width: 1200px; height: 1000px; overflow: hidden; }
  body {
    background: var(--bg);
    font-family: "Nunito Sans", "Avenir Next", Avenir, sans-serif;
    position: relative;
  }
  .card {
    position: absolute;
    left: 230px;
    width: 740px;
    height: 420px;
    border-radius: 26px;
    overflow: hidden;
  }
  .card--front { top: 50px; background: var(--navy); display: flex; align-items: center; justify-content: center; }
  .card--back { top: 530px; display: flex; }
  .wordmark {
    color: var(--white);
    font-weight: 800;
    letter-spacing: -2px;
    line-height: 1;
  }
  .card--front .wordmark { font-size: 150px; }
  .back__brand {
    width: 50%;
    background: var(--navy);
    display: flex;
    align-items: center;
    justify-content: center;
    border-right: 6px solid var(--divider);
  }
  .back__brand .wordmark { font-size: 110px; }
  .back__details {
    width: 50%;
    background: linear-gradient(180deg, var(--paper) 0%, var(--white) 45%, var(--paper-shade) 100%);
    padding: 100px 0 0 44px;
    color: var(--ink);
  }
  .person__name { font-size: 30px; font-weight: 600; line-height: 1.1; }
  .person__role { font-size: 18px; color: var(--muted); margin-bottom: 28px; }
  .contact { list-style: none; }
  .contact__item {
    display: flex;
    align-items: center;
    gap: 10px;
    font-size: 21px;
    margin-bottom: 8px;
  }
  .contact__icon { width: 26px; height: 26px; flex: none; }
</style>
</head>
<body>
  <section class="card card--front">
    <span class="wordmark">pexla</span>
  </section>

  <section class="card card--back">
    <div class="back__brand">
      <span class="wordmark">pexla</span>
    </div>
    <div class="back__details">
      <p class="person__name">Daniel Reyes</p>
      <p class="person__role">Managing Director</p>
      <ul class="contact">
        <li class="contact__item">
          <svg class="contact__icon" viewBox="0 0 26 26"><circle cx="13" cy="13" r="12" fill="none" stroke="#14163f" stroke-width="1.5"/><rect x="9" y="6" width="8" height="14" rx="1.5" fill="none" stroke="#14163f" stroke-width="1.5"/></svg>
          800-555-0142
        </li>
        <li class="contact__item">
          <svg class="contact__icon" viewBox="0 0 26 26"><circle cx="13" cy="13" r="12" fill="none" stroke="#14163f" stroke-width="1.5"/><rect x="7" y="9" width="12" height="8" fill="none" stroke="#14163f" stroke-width="1.5"/><path d="M7 9 L13 14 L19 9" fill="none" stroke="#14163f" stroke-width="1.5"/></svg>
          daniel@pexlamail.com
        </li>
        <li class="contact__item">
          <svg class="contact__icon" viewBox="0 0 26 26"><circle cx="13" cy="13" r="12" fill="none" stroke="#14163f" stroke-width="1.5"/><circle cx="13" cy="13" r="7" fill="none" stroke="#14163f" stroke-width="1.3"/><ellipse cx="13" cy="13" rx="3" ry="7" fill="none" stroke="#14163f" stroke-width="1.3"/><path d="M6 13 H20" stroke="#14163f" stroke-width="1.3"/></svg>
          www.pexla.com
        </li>
      </ul>
    </div>
  </section>
</body>
</html>
```